New Home Subdivision Sign for Larchmere Fields

I need a sign designed for a new home subdivision called Larchmere Fields. It is a family subdivision with many kids. Homes are average size. It is located in a small town.
I will have a tag line so please leave a space for just one sentence.
I have attached the subdivision logo (Larchmere Fields) and the builder logo (Belvix Homes). The subdivision logo has two options (vertical and horizontal), choose whichever fits best for you.
I will need a spot on the sign for a site map. The site map is not completed yet but should be ready in a week and I can send it to you then.
There are no roses in this subdivision. The name is because the original owner of the land had the last name Halbrook. The logo plays off the name but please no other "rose" inspiration
Along the very bottom (no more than 1 foot tall) I need my real estate company info. When you get to that point I will send the files and info but it should all fit within the bottom banner.
Sign is 5' x 8'
Thank you
Target Market(s)
Families
Industry/Entity Type
New Home Construction
Requirements
Must have
- Larchmere Fields logo, space for Realtor info in bottom 12 inches, space for site map that will be provided next week.
Nice to have
- I like the idea of a picture of a family. I also need a tag line for the subdivision so I'm open to ideas on that too

```html
<!DOCTYPE html>
<html lang="en">
<head>
<meta charset="utf-8">
<title>Larchmere Fields – Subdivision Sign</title>
<link rel="stylesheet" href="https://fonts.googleapis.com/css2?family=Montserrat:wght@500;600;700&family=Great+Vibes&family=Libre+Baskerville&display=swap">
<style>
  :root{
    --maroon:#7d0420;
    --green:#6cb33f;
    --green-dark:#4f9a2e;
    --ink:#1c1c1c;
    --paper:#ffffff;
    --mist:#eeeeef;
    --map:#d7ece9;
  }
  *{box-sizing:border-box;margin:0;padding:0}
  html,body{width:818px;height:1200px;overflow:hidden;background:var(--paper)}
  .sign{position:relative;width:818px;height:1200px;background:linear-gradient(180deg,var(--paper) 0%,var(--paper) 60%,var(--mist) 100%);font-family:"Montserrat",sans-serif;color:var(--ink);overflow:hidden}
  .scenery{position:absolute;left:0;top:0;width:818px;height:820px}
  .brand{position:absolute;left:110px;top:70px;display:flex;align-items:center;gap:22px}
  .brand-dot{width:96px;height:96px;border-radius:50%;background:var(--maroon)}
  .brand-name{display:flex;flex-direction:column;align-items:center}
  .brand-name .main{font-weight:700;font-size:52px;letter-spacing:2px;color:var(--maroon);line-height:1}
  .brand-name .sub{font-weight:700;font-size:30px;letter-spacing:9px;color:var(--maroon);line-height:1;margin-top:10px;display:flex;align-items:center;gap:16px}
  .brand-name .sub::before,.brand-name .sub::after{content:"";width:80px;height:2px;background:var(--maroon)}
  .tagline{position:absolute;left:352px;top:285px;width:400px;color:var(--ink)}
  .tagline .script{font-family:"Great Vibes",cursive;font-size:66px;line-height:1;display:block}
  .tagline .serif{font-family:"Libre Baskerville",serif;font-size:30px;display:block;margin:-6px 0 0 120px}
  .builder{position:absolute;left:0;width:818px;top:805px;text-align:center}
  .builder .main{font-weight:500;font-size:92px;letter-spacing:1px;line-height:1;color:var(--ink)}
  .builder .sub{font-weight:600;font-size:30px;letter-spacing:24px;margin-top:12px;display:flex;justify-content:center;align-items:center;gap:14px;padding-left:24px}
  .builder .sub::before,.builder .sub::after{content:"";width:54px;height:3px;background:var(--ink)}
  .agent{position:absolute;left:60px;top:998px;width:320px}
  .agent .company{font-weight:500;font-size:15px;letter-spacing:.3px}
  .agent .name{display:inline-block;margin-top:12px;background:var(--green);color:#fff;font-weight:700;font-size:16px;padding:3px 42px 2px 14px;clip-path:polygon(0 0,86% 0,100% 100%,0 100%)}
  .agent .phone{display:flex;align-items:center;gap:8px;background:var(--maroon);color:#fff;font-weight:700;font-size:24px;padding:3px 14px;width:272px}
  .agent .phone svg{flex:none}
  .agent .contacts{margin-top:12px;display:flex;align-items:center;gap:22px}
  .agent .lines{font-size:14.5px;line-height:1.65}
  .agent .lines span{display:flex;align-items:center;gap:8px}
  .badge{width:26px;height:30px;background:var(--ink)}
  .divider{position:absolute;left:391px;top:990px;width:2px;height:174px;background:var(--maroon)}
  .sitemap{position:absolute;left:423px;top:994px;width:322px;height:154px;background:linear-gradient(180deg,var(--map),#eef6f5);border-radius:4px;display:flex;align-items:center;justify-content:center}
  .sitemap p{font-weight:500;font-size:32px;color:#000}
</style>
</head>
<body>
<div class="sign">
  <svg class="scenery" viewBox="0 0 818 820" aria-hidden="false">
    <defs>
      <linearGradient id="photoTone" x1="1" y1="0" x2="0" y2="1">
        <stop offset="0" stop-color="#f3d27a"/>
        <stop offset=".35" stop-color="#b9a04a"/>
        <stop offset=".7" stop-color="#7fa33a"/>
        <stop offset="1" stop-color="#a6c94a"/>
      </linearGradient>
    </defs>
    <rect x="0" y="200" width="818" height="620" fill="url(#photoTone)" role="img" aria-label="Photo of a smiling family with two children blowing bubbles on a sunny meadow"/>
    <circle cx="624" cy="365" r="100" fill="#ffffff" opacity=".55"/>
    <circle cx="476" cy="413" r="45" fill="#ffffff" opacity=".45"/>
    <path d="M0 0H818V270C800 250 760 222 700 220C600 215 520 265 400 290C250 320 120 290 0 207Z" fill="#ffffff"/>
    <path d="M0 207C120 290 250 320 400 290C520 265 600 215 700 220C760 222 800 250 818 270L818 285C760 250 700 240 620 255C500 280 420 320 300 330C180 338 80 300 0 235Z" fill="var(--maroon)"/>
    <path d="M0 600C60 700 170 785 300 792C450 800 600 692 720 690C770 690 800 720 818 745V820H0Z" fill="var(--green)"/>
    <path d="M0 612C70 712 180 775 300 780C450 788 600 682 720 680C775 680 805 712 818 735" fill="none" stroke="var(--green-dark)" stroke-width="4"/>
    <path d="M0 622C80 725 185 790 300 800C450 810 600 705 720 703C770 703 800 730 818 758V820H0Z" fill="#ffffff"/>
  </svg>

  <div class="brand">
    <div class="brand-dot"></div>
    <div class="brand-name">
      <span class="main">LARCHMERE</span>
      <span class="sub">FIELDS</span>
    </div>
  </div>

  <div class="tagline">
    <span class="script">Home away</span>
    <span class="serif">From Home</span>
  </div>

  <div class="builder">
    <div class="main">BELVIX</div>
    <div class="sub">HOMES</div>
  </div>

  <div class="agent">
    <div class="company">REAL ESTATE COMPANY LOGO</div>
    <div class="name">MARTEN VALE</div>
    <div class="phone">
      <svg width="24" height="24" viewBox="0 0 24 24"><circle cx="12" cy="12" r="10" fill="none" stroke="#fff" stroke-width="2"/><path d="M8.5 7.5l2 2-1 1.5c.8 1.6 1.9 2.7 3.5 3.5l1.5-1 2 2-1.3 1.5C11.5 16.5 7.5 12.5 7 8.8Z" fill="#fff"/></svg>
      0198 765 432
    </div>
    <div class="contacts">
      <div class="lines">
        <span><svg width="14" height="10" viewBox="0 0 14 10"><rect x=".5" y=".5" width="13" height="9" fill="none" stroke="var(--maroon)"/><path d="M.5 .5L7 6l6.5-5.5" fill="none" stroke="var(--maroon)"/></svg>hello@homeagentco.com</span>
        <span><svg width="14" height="14" viewBox="0 0 14 14"><circle cx="7" cy="7" r="6" fill="none" stroke="var(--maroon)" stroke-width="1.3"/><path d="M1 7h12M7 1c-3 3.5-3 8.5 0 12M7 1c3 3.5 3 8.5 0 12" fill="none" stroke="var(--maroon)"/></svg>www.homeagentco.com</span>
      </div>
      <div class="badge"></div>
    </div>
  </div>

  <div class="divider"></div>

  <div class="sitemap" role="img" aria-label="Subdivision site map with numbered lots">
    <p>site map here</p>
  </div>
</div>
</body>
</html>
```